Professional BIO Template with photo and logo

Hello,
I need a professional Bio template developed via Microsoft WORD ASAP!!!!! I would like to just be able to add the text I need to add. So resize-able text boxes. Potentially able to adjust the font. These are the things I need added it to include.
Head shot (attached)
Text Box for Name
Text Box for phone number
Text box for email
KVT Logo (attached)
Maybe a blue banner at the top or some background boxes that are blue or grey. Here are the pantone colors that our company uses.

CORE COLOR
100c 91m 17y 6k 38r 58g 128b Hex #263A80 Pantone 7687 C

CORE CONTRAST COLOR
36c 29m 28y 0k 168r 168g 170b Hex #669999 Pantone Cool Gray 6C

I also attached some examples of what we have been looking at. Instead of green add the blue...instead of black maybe just be white.

Thank you

```html
<!DOCTYPE html>
<html lang="en">
<head>
<meta charset="utf-8">
<title>Dana Whitford – Professional Bio</title>
<link href="https://fonts.googleapis.com/css2?family=Bebas+Neue&family=Montserrat:wght@400;600;700;800&display=swap" rel="stylesheet">
<style>
  :root {
    --core-blue: #263A80;
    --core-blue-deep: #1f2f6e;
    --contrast-grey: #A8A8AA;
    --rule-grey: #B9B9BB;
    --ink: #1c1c1c;
    --paper: #ffffff;
  }
  * { box-sizing: border-box; margin: 0; padding: 0; }
  html, body { width: 922px; height: 1200px; overflow: hidden; background: var(--paper); }
  .bio-sheet {
    position: relative; width: 922px; height: 1200px; overflow: hidden;
    background: var(--paper);
    font-family: "Montserrat", Arial, sans-serif; color: var(--ink);
  }
  .header-band {
    position: absolute; left: 0; top: 0; width: 922px; height: 204px;
    background: linear-gradient(100deg, var(--core-blue-deep) 0%, var(--core-blue) 45%, #3a4f96 100%);
  }
  .header-rule { position: absolute; left: 0; top: 209px; width: 922px; height: 6px; background: var(--rule-grey); }
  .headshot-frame {
    position: absolute; left: 42px; top: 42px; width: 236px; height: 273px;
    border: 1px solid var(--rule-grey); background: var(--paper);
  }
  .headshot {
    position: absolute; left: 11px; top: 17px; width: 211px; height: 240px;
    background: linear-gradient(160deg, #5a5d62 0%, #3b3e43 55%, #23252a 100%);
  }
  .person-name {
    position: absolute; left: 322px; top: 70px;
    font-family: "Bebas Neue", "Oswald", sans-serif; font-size: 72px; line-height: 1;
    color: var(--paper); letter-spacing: 0.5px;
  }
  .person-contact {
    position: absolute; left: 322px; top: 140px;
    font-weight: 800; font-size: 23px; color: var(--contrast-grey); letter-spacing: 0.3px;
  }
  .bio-body {
    position: absolute; left: 317px; top: 262px; width: 561px;
    font-size: 13.2px; line-height: 17px; text-align: justify;
  }
  .bio-body p { margin-bottom: 17px; }
  .sidebar {
    position: absolute; left: 42px; top: 339px; width: 234px; height: 693px;
    box-shadow: 0 0 6px rgba(0,0,0,0.35);
  }
  .sidebar-block { color: var(--paper); font-size: 12.2px; line-height: 15.4px; padding: 22px 16px 10px 16px; }
  .sidebar-block p + p { margin-top: 15px; }
  .sidebar-block--grey { background: var(--contrast-grey); }
  .sidebar-block--blue { background: var(--core-blue); }
  .sidebar-block--intro { height: 201px; }
  .sidebar-block--mid { height: 183px; padding-top: 14px; }
  .sidebar-block--tail { height: 309px; padding-top: 14px; position: relative; }
  .skyline-art {
    position: absolute; left: 40px; bottom: 0; width: 150px; height: 65px;
    background: linear-gradient(180deg, rgba(255,255,255,0.15), rgba(255,255,255,0.45));
  }
  .highlight-panel {
    position: absolute; left: 276px; top: 769px; width: 646px; height: 161px;
    background: var(--core-blue); color: var(--paper);
    padding: 17px 40px 0 41px; font-weight: 700; font-size: 13.2px; line-height: 17px; text-align: justify;
  }
  .highlight-panel p + p { margin-top: 17px; }
  .pull-quote {
    position: absolute; left: 314px; top: 945px; width: 560px;
    color: var(--core-blue); font-weight: 700; font-size: 16.4px; line-height: 22px;
  }
  .brand-mark {
    position: absolute; left: 677px; top: 1050px; width: 158px; height: 96px;
    display: flex; align-items: center; justify-content: center; gap: 12px;
    background: var(--paper);
  }
  .brand-mark__square { width: 22px; height: 22px; border: 2px solid var(--core-blue); }
  .brand-mark__name { font-weight: 800; font-size: 38px; color: var(--core-blue); letter-spacing: 1px; }
  .footer-art { position: absolute; left: 0; top: 1030px; width: 922px; height: 170px; }
</style>
</head>
<body>
<main class="bio-sheet">
  <div class="header-band" role="img" aria-label="Blue banner with faint architectural glass-roof lines"></div>
  <div class="header-rule"></div>

  <div class="headshot-frame">
    <div class="headshot" role="img" aria-label="Head shot portrait of Dana Whitford"></div>
  </div>

  <h1 class="person-name">DANA WHITFORD</h1>
  <p class="person-contact">PHONE NUMBER &nbsp;|&nbsp; EMAIL</p>

  <section class="bio-body">
    <p>Lorem ipsum dolor sit amet, consectetuer adipiscing elit, sed diam nonummy nibh euismod tincidunt ut laoreet dolore magna aliquam erat volutpat. Ut wisi enim ad minim veniam, quis nostrud exerci tation ullamcorper suscipit lobortis nisl ut aliquip ex ea commodo consequat.</p>
    <p>Duis autem vel eum iriure dolor in hendrerit in vulputate velit esse molestie consequat, vel illum dolore eu feugiat nulla facilisis at vero eros et accumsan et iusto odio.</p>
    <p>Lorem ipsum dolor sit amet, consectetuer adipiscing elit, sed diam nonummy nibh euismod tincidunt ut laoreet dolore magna aliquam erat volutpat. Ut wisi enim ad minim veniam, quis nostrud exerci tation ullamcorper suscipit lobortis nisl ut aliquip ex ea commodo consequat. Duis autem vel eum iriure dolor in hendrerit in vulputate velit esse molestie consequat, vel illum dolore eu feugiat nulla facilisis at vero eros et accumsan et iusto odio dignissim qui blandit praesent luptatum zzril delenit augue duis dolore te feugait nulla facilisi.</p>
    <p>Lorem ipsum dolor sit amet, cons ectetuer adipiscing elit, sed diam nonummy nibh euismod tincidunt ut laoreet dolore magna aliquam erat volutpat. Ut wisi enim ad minim veniam, quis nostrud exerci tation ullamcorper suscipit lobortis nisl ut aliquip ex ea commodo consequat.</p>
    <p>Lorem ipsum dolor sit amet, cons ectetuer adipiscing elit, sed diam nonummy nibh euismod tincidunt ut laoreet dolore magna aliquam erat volutpat. Ut wisi enim ad minim veniam, quis nostrud exerci tation ullamcorper suscipit lobortis.</p>
  </section>

  <aside class="sidebar">
    <div class="sidebar-block sidebar-block--grey sidebar-block--intro">
      <p>Lorem ipsum dolor sit amet, consectetuer adipiscing elit, sed diam nonummy nibh euismod tincidunt ut laoreet dolore magna aliquam erat volutpat. Ut wisi enim ad minim veniam, quis nostrud exerci tation ullamcorper suscipit lobortis nisl ut aliquip ex ea commodo consequat.</p>
    </div>
    <div class="sidebar-block sidebar-block--blue sidebar-block--mid">
      <p>Lorem ipsum dolor sit amet, consectetuer adipiscing elit, sed diam nonummy nibh euismod tincidunt ut laoreet dolore magna aliquam erat volutpat. Ut wisi enim ad minim veniam, quis nostrud exerci tation ullamcorper suscipit lobortis nisl ut aliquip ex ea commodo consequat.</p>
    </div>
    <div class="sidebar-block sidebar-block--grey sidebar-block--tail">
      <p>Lorem ipsum dolor sit amet, consectetuer adipiscing elit, sed diam nonummy nibh euismod tincidunt ut laoreet dolore magna aliquam erat volutpat.</p>
      <p>Lorem ipsum dolor sit amet, consectetuer adipiscing elit, sed diam nonummy nibh euismod tincidunt ut laoreet dolore magna aliquam erat volutpat.</p>
      <div class="skyline-art" role="img" aria-label="White outline of a city skyline"></div>
    </div>
  </aside>

  <section class="highlight-panel">
    <p>Lorem ipsum dolor sit amet, consectetuer adipiscing elit, sed diam nonummy nibh euismod tincidunt ut laoreet dolore magna aliquam erat volutpat. Ut wisi enim ad minim veniam, quis nostrud exerci tation ullamcorper suscipit lobortis nisl ut aliquip ex ea commodo consequat.</p>
    <p>Lorem ipsum dolor sit amet, consectetuer adipiscing elit, sed diam nonummy nibh euismod tincidunt ut laoreet dolore magna aliquam erat volutpat.</p>
  </section>

  <p class="pull-quote">Duis autem vel eum iriure dolor in hendrerit in vulputate velit esse molestie consequat, vel illum dolore eu feugiat nulla facilisis at vero eros et accumsan et iusto odio.</p>

  <svg class="footer-art" viewBox="0 0 922 170" aria-hidden="true">
    <rect x="244" y="52" width="408" height="33" fill="var(--core-blue)"/>
    <rect x="862" y="52" width="60" height="33" fill="var(--core-blue)"/>
    <rect x="0" y="85" width="244" height="32" fill="var(--contrast-grey)"/>
    <polygon points="165,150 280,35 230,60 200,100" fill="#e4e4e6"/>
    <polygon points="165,150 280,35 300,35 180,160" fill="#ffffff"/>
    <rect x="0" y="141" width="922" height="5" fill="var(--rule-grey)"/>
    <rect x="0" y="152" width="922" height="18" fill="var(--core-blue)"/>
  </svg>

  <div class="brand-mark">
    <span class="brand-mark__square"></span>
    <span class="brand-mark__name">KVT</span>
  </div>
</main>
</body>
</html>
```